Meridian Vault Data Works Needs a Website Desing

We need a website design for a new company based in Kuwait called Meridian Vault Data Works (MVDW). We provide Software as a Service (SaaS) solutions for small and medium business companies. We will develop the required E-systems like HR,Payroll,Accounting Systems for those customers who wants to focus on their business instead of wasting time to automate it. MVDW need a web site that represent this activity and showing our cloud products and allow out customers to easily identify their needs. as a normal web site basic things need to be included like :
about MVDW
Solutions
PressRoom
Contact us
please i need something similar to tralvex.com or ozk.com or www.plorvane.com with blue and black theme .. please check the Company's logo
hi all ,,,
the project is only design without any codes
Reason: The project is focus on design only ,, i will be really appreciated to have more designs

```html
<!DOCTYPE html>
<html lang="en">
<head>
<meta charset="utf-8">
<title>Meridian Vault Data Works</title>
<link href="https://fonts.googleapis.com/css2?family=Roboto+Condensed:wght@300;400;700&family=Arimo:wght@400;700&display=swap" rel="stylesheet">
<style>
:root{
  --blue:#0aaef0;
  --blue-deep:#0593d6;
  --blue-text:#129be0;
  --ink:#222;
  --heading:#555;
  --body:#666;
  --rule:#ddd;
  --btn:#2e2e2e;
  --band:#f4f4f4;
  --footer:#050505;
  --social:#7a7a7a;
}
*{margin:0;padding:0;box-sizing:border-box}
html,body{width:1200px;height:1116px;overflow:hidden;background:#fff}
body{position:relative;font-family:"Arimo",Arial,sans-serif;color:var(--body)}
.site-header{position:absolute;left:0;top:0;width:1200px;height:130px;background:linear-gradient(#e2e2e2,#fafafa 70%,#fff)}
.brand{position:absolute;left:130px;top:31px;display:flex;align-items:center;gap:10px}
.brand-mark{width:62px;height:62px;border-radius:50%;background:var(--blue-deep)}
.brand-text{color:var(--ink);font-family:"Roboto Condensed",sans-serif;font-weight:700;line-height:1}
.brand-name{font-size:46px;letter-spacing:1px}
.brand-full{font-size:11px;margin-top:3px}
.main-nav{position:absolute;top:54px;left:0}
.main-nav a{position:absolute;white-space:nowrap;font-family:"Roboto Condensed",sans-serif;font-size:14px;color:#333;text-decoration:none;text-transform:uppercase}
.hero{position:absolute;left:0;top:130px;width:1200px;height:431px;background:radial-gradient(ellipse at 60% 45%,#3cc4f7,var(--blue) 45%,var(--blue-deep) 100%)}
.hero-title{position:absolute;left:128px;top:66px;font-family:"Roboto Condensed",sans-serif;font-weight:300;font-size:37px;line-height:43px;color:#fff;text-transform:uppercase}
.hero-copy{position:absolute;left:126px;top:176px;width:420px;font-family:"Roboto Condensed",sans-serif;font-size:14px;line-height:20px;color:#fff;text-align:justify}
.learn-more{position:absolute;left:126px;top:313px;width:150px;height:41px;border-radius:3px;background:linear-gradient(#fff,#dcdcdc);display:flex;align-items:center;padding-left:12px;font-family:"Roboto Condensed",sans-serif;font-weight:700;font-size:18px;color:#444}
.learn-more svg{position:absolute;right:9px;top:9px}
.hero-visual{position:absolute;left:565px;top:80px;width:515px;height:300px;border-radius:8px;background:radial-gradient(ellipse at 50% 45%,#1b5fe0,#1c86e8 55%,rgba(10,174,240,0) 75%)}
.slider-dots{position:absolute;left:562px;top:400px;display:flex;gap:9px}
.slider-dots span{width:12px;height:12px;border-radius:50%;background:#0a86c0}
.slider-dots .active{background:#ddd}
.features{position:absolute;left:0;top:561px;width:1200px;height:354px}
.feature{position:absolute;top:0;width:301px;height:354px}
.feature h2{position:absolute;top:20px;left:0;font-family:"Roboto Condensed",sans-serif;font-weight:400;font-size:22px;color:var(--heading)}
.feature hr{position:absolute;top:57px;left:0;width:301px;border:0;border-top:1px solid var(--rule)}
.feature .lead{position:absolute;left:0;width:300px;font-size:12px;line-height:18px;color:var(--blue-text);text-align:justify}
.feature .text{position:absolute;left:0;width:300px;font-size:12px;line-height:18px;color:var(--body);text-align:justify}
.read-more{position:absolute;top:308px;left:0;width:89px;height:32px;background:var(--btn);color:#fff;font-family:"Roboto Condensed",sans-serif;font-size:12px;display:flex;align-items:center;justify-content:center}
.video-frame{position:absolute;left:-1px;top:78px;width:302px;height:205px;border:1px solid #ddd;padding:4px;background:#fff;box-shadow:0 1px 2px rgba(0,0,0,.1)}
.video-still{position:relative;width:100%;height:100%;background:radial-gradient(ellipse at 50% 40%,#e9f3fb,#8ebbe3 60%,#4f86c2)}
.video-still svg{position:absolute;left:113px;top:75px}
.clients{position:absolute;left:0;top:915px;width:1200px;height:144px;background:linear-gradient(#e4e4e4,#fafafa 18px,#fff)}
.client{position:absolute;top:70px;transform:translate(-50%,-50%);white-space:nowrap;font-family:"Roboto Condensed",sans-serif;font-weight:700;font-size:15px;color:#555}
.site-footer{position:absolute;left:0;top:1059px;width:1200px;height:57px;background:var(--footer)}
.copyright{position:absolute;left:120px;top:16px;font-size:14px;color:#ccc}
.social{position:absolute;left:930px;top:9px;display:flex;gap:8px}
.social span{width:32px;height:32px;border-radius:50%;background:var(--social)}
</style>
</head>
<body>
<header class="site-header">
  <div class="brand">
    <div class="brand-mark"></div>
    <div class="brand-text">
      <div class="brand-name">MVDW</div>
      <div class="brand-full">Meridian Vault Data Works</div>
    </div>
  </div>
  <nav class="main-nav">
    <a style="left:541px">Home</a>
    <a style="left:626px">About MVDW</a>
    <a style="left:751px">Solutions</a>
    <a style="left:867px">Pressroom</a>
    <a style="left:990px">Contact Us</a>
  </nav>
</header>

<section class="hero">
  <h1 class="hero-title">We are cloud computing<br>company providing SaaS</h1>
  <p class="hero-copy">Lorem ipsum dolor sit amet, consectetur adipisicing elit, sed do eiusmod tempor incididunt ut labore et dolore magna aliqua. Ut enim ad minim veniam, quis nostrud exercitation ullamco laboris nisi ut aliquip ex ea commodo consequat. Duis aute irure dolor in reprehenderit in voluptate velit esse</p>
  <div class="learn-more">LEARN MORE
    <svg width="24" height="24" viewBox="0 0 24 24"><circle cx="12" cy="12" r="11" fill="#c8c8c8"/><path d="M10 7l5 5-5 5" fill="none" stroke="#fff" stroke-width="2.5"/></svg>
  </div>
  <div class="hero-visual" role="img" aria-label="Tablet, desktop monitor, laptop and phone showing blue cloud screens"></div>
  <div class="slider-dots"><span></span><span></span><span class="active"></span><span></span></div>
</section>

<section class="features">
  <article class="feature" style="left:120px">
    <h2>WELCOME!</h2><hr>
    <p class="lead" style="top:76px">Et magnis dis parturient montes, nascetur ridic ulus mus. Nulla dui.&nbsp; Et magnis dis parturient montes, nascetur ridic ulus mus. Nulla dui.</p>
    <p class="text" style="top:148px">Fusce suscipit varius mi. Cum sociis natoque penatibus et magnis dis parturient montes, nascetur ridic ulus mus. Nulla dui. mauris.</p>
    <p class="text" style="top:220px">Fusce suscipit varius mi. Cum sociis natoque penatibus et magnis dis parturient montes, nascetur ridic ulus mus. Nulla dui. mauris.Fusce suscipit varius mi. Cum sociis natoque penatibus et magnis dis parturient montes,</p>
    <div class="read-more">READ MORE</div>
  </article>
  <article class="feature" style="left:450px">
    <h2>HOW IT WORKS</h2><hr>
    <div class="video-frame">
      <div class="video-still" role="img" aria-label="Video still of a laptop among bright clouds">
        <svg width="62" height="42" viewBox="0 0 62 42"><rect width="62" height="42" rx="8" fill="#333" opacity=".85"/><path d="M24 11l16 10-16 10z" fill="#eee"/></svg>
      </div>
    </div>
    <div class="read-more">READ MORE</div>
  </article>
  <article class="feature" style="left:782px">
    <h2 style="left:6px">SOLUTIONS</h2><hr>
    <p class="lead" style="top:80px">Et magnis dis parturient montes, nascetur ridic ulus mus. Nulla dui. Praesent vestibulum molestie. Lorem ipsum dolor sit amet, consec tetuer adipiscing elit. Praesent ves tibulum molestie lacus.</p>
    <p class="text" style="top:170px">Fusce suscipit varius mi. Cum sociis natoque penatibus et magnis dis parturient montes, nascetur ridic ulus mus. Nulla dui. mauris.Fusce suscipit varius mi. Cum sociis natoque penatibus et magnis dis parturient montes, nascetur ridic ulus mus. Nulla dui. mauris.Fusce suscipit varius mi. Cum sociis natoque penatibus et magnis dis parturient montes,</p>
    <div class="read-more">READ MORE</div>
  </article>
</section>

<section class="clients">
  <span class="client" style="left:154px">Corvane</span>
  <span class="client" style="left:250px">Ulvo</span>
  <span class="client" style="left:347px">Tessaline</span>
  <span class="client" style="left:448px">Terra Atlas</span>
  <span class="client" style="left:552px">Brightwell</span>
  <span class="client" style="left:638px">Savora</span>
  <span class="client" style="left:732px">Kelvo</span>
  <span class="client" style="left:828px">Quorix</span>
  <span class="client" style="left:925px">Ostara</span>
  <span class="client" style="left:1032px">Valdrin</span>
</section>

<footer class="site-footer">
  <p class="copyright">© 2013 MVDW. | All Rights Reserved.</p>
  <div class="social">
    <span aria-label="Friendloop"></span>
    <span aria-label="Chirpline"></span>
    <span aria-label="Circlet"></span>
    <span aria-label="Viewcast"></span>
  </div>
</footer>
</body>
</html>
```